Blockchain Analytics Firm Needs Logo And Website Design

We need a logo and a very basic website for a company based in Linköping, Sweden called 'Vextor'. We build custom machine learning and AI solutions for companies based on blockchain. We are not picky about the colors, but the design should communicate modernity and stability.
We like the following websites:
https://www.pallidwren.co.uk/
https://www.tormacapitalhouse.com/
Target Market(s)
Our customers are startups that have their own product based on blockchain or other distributed ledger technology.
Industry/Entity Type
It Company
Contact Information for Business Card
Name, title and email address
Logo Text
Our company name and "Blockchain Analytics"
Font styles to use
Colors
Designer to choose colors to be used in the design.
Requirements
Must have
- The website and logo need to be modern and clean. In the beginning, we will not be filling out all sections of the website (team, clients, etc.) but we will need to have these set up so we can eventually use them.
Nice to have
- We like angular graphics and some animations on the webpage would be nice.

```html
<!DOCTYPE html>
<html lang="en">
<head>
<meta charset="utf-8">
<title>Vextor – Blockchain Analytics</title>
<link href="https://fonts.googleapis.com/css2?family=Lato:wght@400;700;900&display=swap" rel="stylesheet">
<style>
:root{
  --ink:#2b2b2b;
  --header:#2a2a2a;
  --night:#1e1e1e;
  --footer:#151515;
  --red:#e8414a;
  --blue:#1a82c4;
  --purple:#5b0ea6;
  --peach:#fdeee8;
  --white:#ffffff;
  --muted:#8a8a8a;
  --line:#9a9a9a;
}
*{margin:0;padding:0;box-sizing:border-box}
html,body{width:1200px;height:3383px;overflow:hidden}
body{font-family:'Lato',sans-serif;color:var(--ink);background:var(--white);position:relative}
.abs{position:absolute}
.site-header{left:0;top:0;width:1200px;height:129px;background:var(--header)}
.brand{left:72px;top:30px;display:flex;align-items:center;gap:14px}
.brand-dot{width:58px;height:58px;border-radius:50%;background:var(--red)}
.brand-name{font-size:30px;font-weight:700;color:var(--red);line-height:1;letter-spacing:1px}
.brand-tag{font-size:21px;color:var(--blue);line-height:1.2}
.header-icons{right:72px;top:52px;display:flex;gap:28px}
.header-icons svg{width:26px;height:26px}
.shapes{left:0;top:0}
.hero-title{left:165px;top:278px;font-size:46px;font-weight:400;color:var(--red);letter-spacing:2px;line-height:1}
.hero-sub{left:165px;top:330px;font-size:34px;color:var(--blue);line-height:1}
.hero-text{left:165px;top:376px;width:400px;font-size:20px;line-height:1.35;color:var(--ink)}
.btn{left:165px;top:456px;width:151px;height:42px;background:var(--blue);color:var(--white);font-size:12px;font-weight:700;letter-spacing:1px;display:flex;align-items:center;justify-content:center}
.hero-media{left:559px;top:225px;width:564px;height:340px;border:6px solid var(--white);box-shadow:0 4px 16px rgba(0,0,0,.35);background:linear-gradient(135deg,#2f4f7a 0%,#6f8fb4 45%,#c0392b 60%,#1f2f4a 100%)}
.about-title{left:512px;top:928px;font-size:30px;color:var(--white);line-height:1.3}
.about-text{left:512px;top:1025px;width:620px;font-size:14.5px;line-height:27px;color:#e8e8e8}
.ml-title{left:75px;top:1340px;font-size:32px;color:var(--white)}
.ml-text{left:75px;top:1397px;width:600px;font-size:13.5px;font-weight:700;line-height:27px;color:var(--white)}
.ml-icon{left:765px;top:1268px;width:292px;height:276px;border-radius:18px;background:linear-gradient(135deg,#1f3a55,#243240)}
.ai-icon{left:124px;top:1827px;width:282px;height:282px;border-radius:18px;background:linear-gradient(135deg,#f9d6d3,#f6c0bc)}
.ai-title{right:72px;top:1856px;font-size:32px;color:var(--white)}
.ai-text{right:72px;top:1914px;width:640px;text-align:right;font-size:13.5px;font-weight:700;line-height:28px;color:var(--white)}
.testimonial{left:0;top:2215px;width:1200px;height:334px;background:radial-gradient(ellipse at 70% 60%,#1f3346 0%,#0f1822 55%,#0a0f15 100%)}
.avatar{left:550px;top:2285px;width:100px;height:100px;border-radius:50%;border:4px solid #d8d8d8;background:linear-gradient(180deg,#7d7d7d,#3c3c3c)}
.quote{left:130px;top:2403px;width:940px;text-align:center;font-size:14.5px;line-height:27px;color:var(--white)}
.quote-name{left:0;top:2472px;width:1200px;text-align:center;font-size:15px;color:var(--blue)}
.blog-title{left:75px;top:2598px;font-size:30px;color:var(--ink)}
.blog-arrows{left:1078px;top:2607px;display:flex;gap:10px}
.post{top:2680px;width:512px}
.post-media{width:512px;height:214px}
.post-head{margin-top:22px;font-size:20px;font-weight:700;color:var(--blue)}
.post-text{margin-top:8px;font-size:13.5px;line-height:24px;color:var(--ink)}
.post-meta{margin-top:14px;display:flex;justify-content:space-between;font-size:13px;color:var(--red)}
.post-meta span{display:flex;align-items:center;gap:8px}
.site-footer{left:0;top:3135px;width:1200px;height:248px;background:var(--footer)}
.foot-brand{left:75px;top:3183px;display:flex;align-items:center;gap:12px}
.foot-brand .brand-dot{width:48px;height:48px}
.foot-brand .brand-name{font-size:25px}
.foot-brand .brand-tag{font-size:17px}
.copy{left:75px;top:3255px;font-size:12px;line-height:20px;color:#666}
.social{left:75px;top:3310px;display:flex;gap:20px}
.social i{display:block;width:20px;height:20px;border-radius:50%;background:#6a6a6a}
.foot-col{top:3178px;color:#bdbdbd;font-size:13px;line-height:23px}
.foot-col h3{font-size:17px;font-weight:700;color:var(--white);margin-bottom:14px}
.hours-row{display:flex;gap:28px}
.mail{display:flex;align-items:center;gap:12px;margin-top:12px}
.signup{display:flex;margin-top:4px}
.signup .field{width:190px;height:38px;background:var(--white);color:#888;font-size:12px;display:flex;align-items:center;padding-left:10px}
.signup .go{width:40px;height:38px;background:var(--blue);display:flex;align-items:center;justify-content:center}
</style>
</head>
<body>

<header class="abs site-header">
  <div class="abs brand">
    <div class="brand-dot"></div>
    <div><div class="brand-name">VEXTOR</div><div class="brand-tag">Blockchain Analytics</div></div>
  </div>
  <div class="abs header-icons">
    <svg viewBox="0 0 24 24"><circle cx="10" cy="10" r="7" fill="none" stroke="#fff" stroke-width="3"/><line x1="15" y1="15" x2="22" y2="22" stroke="#fff" stroke-width="3"/></svg>
    <svg viewBox="0 0 24 24"><rect x="2" y="4" width="20" height="3" fill="#fff"/><rect x="2" y="11" width="20" height="3" fill="#fff"/><rect x="2" y="18" width="20" height="3" fill="#fff"/></svg>
  </div>
</header>

<svg class="abs shapes" width="1200" height="2215" viewBox="0 0 1200 2215">
  <rect y="1697" width="1200" height="518" fill="var(--peach)"/>
  <g fill="none" stroke="var(--line)" stroke-width="1.5">
    <path d="M1015 130 Q1050 140 1080 190 L1200 360"/>
    <path d="M0 375 L470 790 Q520 830 560 830 L640 830"/>
    <path d="M600 1620 L760 1760"/>
    <path d="M560 1975 L420 2215"/>
  </g>
  <path d="M0 462 L40 462 Q70 462 95 485 L440 800 Q470 830 440 860 L270 1030 L0 1030 Z" fill="var(--purple)"/>
  <path d="M690 655 Q778 600 860 660 L1200 960 L1200 1400 L840 1700 Q800 1730 760 1700 L280 1280 Q240 1225 280 1175 Z" fill="var(--night)"/>
  <path d="M0 1207 L520 1207 Q560 1207 590 1235 L725 1440 Q742 1466 725 1492 L565 1675 Q545 1697 505 1697 L0 1697 Z" fill="var(--red)"/>
  <path d="M1200 1708 L720 1708 Q690 1708 668 1730 L487 1918 Q470 1940 487 1962 L668 2178 Q690 2200 720 2200 L1200 2200 Z" fill="var(--blue)"/>
</svg>

<h1 class="abs hero-title">VEXTOR</h1>
<div class="abs hero-sub">Blockchain Analytics</div>
<p class="abs hero-text">Vivamus lobortis aliquam nulla venenatis porta venenatis tellus malesuada.</p>
<div class="abs btn">LEARN MORE</div>
<div class="abs hero-media" role="img" aria-label="Photo of a businessman running up a red trend arrow beside a large gold coin over a world map"></div>

<h2 class="abs about-title">About<br>Vextor Data Analytic</h2>
<p class="abs about-text">Vextor is a data analytics startup that can quickly deploy custom machine learning and AI solutions for companies based on Distributed Ledger Technologies (DLT) such as Blockchains. A massive amount of data is generated from these Smart Contracts, particularly from Internet of Things (IoT) applications. We combine this information with traditional data pipelines and present a complete package to our customer.</p>

<h2 class="abs ml-title">Machine Learning</h2>
<p class="abs ml-text">Curabitur tempor risus nec ipsum egestas, pellentesque dapibus est bibendum. Nullam condimentum bibendum nisl, at venenatis tellus malesuada a. Aliquam laoreet orci ligula, in sagittis magna vehicula eu. Integer at nisi at libero posuere viverra quis non turpis.</p>
<div class="abs ml-icon" role="img" aria-label="Line illustration of a human head profile with circuits and a gear"></div>

<div class="abs ai-icon" role="img" aria-label="Line illustration of a brain on a microchip"></div>
<h2 class="abs ai-title">AI Solutions</h2>
<p class="abs ai-text">Curabitur tempor risus nec ipsum egestas, pellentesque dapibus est bibendum. Nullam condimentum bibendum nisl, at venenatis tellus malesuada a. Aliquam laoreet orci ligula, in sagittis magna vehicula eu. Integer at nisi at libero posuere viverra quis non turpis.</p>

<section class="abs testimonial" role="img" aria-label="Dark network background for the testimonial"></section>
<div class="abs avatar" role="img" aria-label="Portrait of the client quoted"></div>
<p class="abs quote">“ Curabitur tempor risus nec ipsum egestas, pellentesque dapibus est bibendum. condimentum bibendum nisl, at venenatis tellus malesuada a. Aliquam laoreet orci ligula, in sagittis magna vehicula eu. Integer at nisi at libero posuere...”</p>
<div class="abs quote-name">Name Heading</div>

<h2 class="abs blog-title">Latest from the blog</h2>
<div class="abs blog-arrows">
  <svg width="20" height="20" viewBox="0 0 20 20"><path d="M12 4 L6 10 L12 16 M6 10 H18" fill="none" stroke="#bbb" stroke-width="3"/></svg>
  <svg width="20" height="20" viewBox="0 0 20 20"><path d="M8 4 L14 10 L8 16 M14 10 H2" fill="none" stroke="var(--blue)" stroke-width="3"/></svg>
</div>

<article class="abs post" style="left:75px">
  <div class="post-media" role="img" aria-label="Digital illustration of a glowing coin on a circuit board with icons" style="background:radial-gradient(circle at 50% 45%,#e6c35a 0%,#2a4f6a 35%,#0c1e2c 100%)"></div>
  <h3 class="post-head">Curabitur tempor risus nec ipsum egestas</h3>
  <p class="post-text">Pellentesque dapibus est bibendum condimentum bibendum nisl, at venenatis tellus malesuada a. Aliquam laoreet orci ligula, in sagittis magna vehicula eu. Integer at nisi at libero posuere...</p>
  <div class="post-meta"><span>Continue Reading</span><span><svg width="14" height="12" viewBox="0 0 14 12"><path d="M1 1 H13 V8 H6 L3 11 V8 H1 Z" fill="var(--red)"/></svg>7 Comments</span></div>
</article>

<article class="abs post" style="left:614px">
  <div class="post-media" role="img" aria-label="Photo of a man touching a glowing blockchain interface screen" style="background:linear-gradient(120deg,#0e2a44 0%,#2f6f9e 50%,#12324f 100%)"></div>
  <h3 class="post-head">Curabitur tempor risus nec ipsum egestas</h3>
  <p class="post-text">Pellentesque dapibus est bibendum condimentum bibendum nisl, at venenatis tellus malesuada a. Aliquam laoreet orci ligula, in sagittis magna vehicula eu. Integer at nisi at libero posuere...</p>
  <div class="post-meta"><span>Continue Reading</span><span><svg width="14" height="12" viewBox="0 0 14 12"><path d="M1 1 H13 V8 H6 L3 11 V8 H1 Z" fill="var(--red)"/></svg>7 Comments</span></div>
</article>

<footer class="abs site-footer"></footer>
<div class="abs foot-brand">
  <div class="brand-dot"></div>
  <div><div class="brand-name">VEXTOR</div><div class="brand-tag">Blockchain Analytics</div></div>
</div>
<p class="abs copy">Copyright 2018 Company Name.<br>All Rights Reserved.</p>
<div class="abs social"><i></i><i></i><i></i><i></i><i></i></div>

<div class="abs foot-col" style="left:356px">
  <h3>Address Info</h3>
  <p>Norrvik Innovation Park,<br>Ljusgatan 12, SE-582 40<br>Linköping, SWEDEN</p>
  <div class="mail"><svg width="14" height="11" viewBox="0 0 14 11"><rect width="14" height="11" fill="#bdbdbd"/><path d="M0 0 L7 6 L14 0" fill="none" stroke="#151515" stroke-width="1.5"/></svg>hello@vextor-analytics.se</div>
</div>

<div class="abs foot-col" style="left:625px">
  <h3>Hours</h3>
  <div class="hours-row"><span>Mon–Fri: 9:00AM–5:00PM</span></div>
  <div class="hours-row" style="margin-top:12px"><span>Sat &amp; Sun:</span><span>11:00AM–3:00PM</span></div>
</div>

<div class="abs foot-col" style="left:898px">
  <h3>Email Sign Up</h3>
  <div class="signup"><div class="field">Enter Email Address</div><div class="go"><svg width="10" height="14" viewBox="0 0 10 14"><path d="M2 2 L8 7 L2 12" fill="none" stroke="#fff" stroke-width="2.5"/></svg></div></div>
</div>

</body>
</html>
```